Intranet for company management ERP Style

We need a redesign for our Intranet webpage (Images, CSS), we have all the code and functionality ready and a basic design but it is not good looking. In order to meet our company standards this design has to be fully responsive and elegant, also should display the colors of the company: (#F17808 #EDAA64 #F4B947 #F2A900 #292828 #3D3D3D #062953) usually Dark orange colors are the main ones, though we wouldn't mind to see other options or to implement a pair of skins that we could switch easily on the webpage.
Access to the webpage can be granted

Target Market(s)

this webpage is for internal use of the company but could also be sold to external customers in the future, our market is cryptocurrency and BPO

Industry/Entity Type

BPO, Cryptocurrency

Coding

Coded - Design and coding required

Number of Pages Required

1 page

Font styles to use
Other font styles liked:
• Headings: Montserrat Extra Bold, Sub headings: Montserrat, Text: Object Sans

Colors
F0912C
F2A743
F7CA91
FBE8D2
FDF5EE

Requirements
Nice to have
• elegant icons designs and menus

```html
<!DOCTYPE html>
<html lang="en">
<head>
<meta charset="utf-8">
<title>Northhub Intranet – Suggestion</title>
<link rel="stylesheet" href="https://fonts.googleapis.com/css2?family=Montserrat:wght@500;600;700;800&family=Poppins:wght@400;500&display=swap">
<style>
:root{
  --board:#d8d8d8;
  --sidebar:#292828;
  --orange:#f0912c;
  --orange-deep:#f07050;
  --orange-light:#f4b860;
  --page:#f4f5f9;
  --white:#ffffff;
  --ink:#1f1f1f;
  --muted:#6d6d6d;
  --line:#e6e7ec;
  --accent-red:#ef5a3c;
}
*{box-sizing:border-box;margin:0;padding:0}
html,body{width:1038px;height:1200px;overflow:hidden}
body{background:var(--board);position:relative;font-family:"Poppins",sans-serif;color:var(--ink)}
.screen{position:absolute;left:92px;width:855px;height:428px;background:var(--page);overflow:hidden}
.screen--form{top:122px}
.screen--list{top:632px;height:447px}
.sidebar{position:absolute;left:0;top:0;bottom:0;width:137px;background:var(--sidebar);color:var(--white)}
.brand{position:absolute;top:44px;left:0;width:137px;text-align:center;font-family:"Montserrat",sans-serif;font-weight:700;font-size:16px;letter-spacing:.2px}
.brand-dot{display:block;width:16px;height:16px;border-radius:50%;background:var(--orange);margin:0 auto 8px}
.nav-item{position:absolute;left:0;width:137px;height:20px;display:flex;align-items:center;font-family:"Montserrat",sans-serif;font-weight:600;font-size:10px;transform:translateY(-50%)}
.nav-item svg{position:absolute;left:16px;width:12px;height:12px;fill:currentColor}
.nav-item span{position:absolute;left:39px}
.nav-item.is-active{color:var(--orange)}
.nav-item.is-active::before{content:"";position:absolute;left:0;width:8px;height:6px;border-radius:0 3px 3px 0;background:var(--orange)}
.nav-sub{position:absolute;left:51px;font-family:"Montserrat",sans-serif;font-weight:500;font-size:9px;transform:translateY(-50%)}
.nav-sub.is-active{color:var(--orange)}
.topbar{position:absolute;left:137px;right:0;top:0;height:56px;background:var(--white);border-bottom:1px solid var(--line)}
.topbar .icon{position:absolute;top:21px;width:12px;height:12px;fill:var(--ink)}
.search{position:absolute;left:275px;top:14px;width:305px;height:27px;border-radius:14px;background:#f1f2f5;font-size:8px;color:#8a8a8a;padding-left:14px;line-height:27px}
.search svg{position:absolute;right:12px;top:8px;width:11px;height:11px}
.user{position:absolute;left:754px;top:14px;display:flex;align-items:center;gap:6px;font-family:"Montserrat",sans-serif;font-weight:600;font-size:10px}
.avatar{width:27px;height:27px;border-radius:50%;background:linear-gradient(#cfd3da,#40454f)}
.page-title{position:absolute;left:163px;top:76px;font-family:"Montserrat",sans-serif;font-weight:800;font-size:19px}
.crumb{position:absolute;left:163px;top:103px;font-size:8.5px;color:#444}
.crumb a{color:var(--accent-red);text-decoration:none}
.field-label{position:absolute;font-family:"Montserrat",sans-serif;font-weight:500;font-size:11.5px;transform:translateY(-50%)}
.field{position:absolute;width:330px;height:37px;background:var(--white);box-shadow:0 2px 6px rgba(0,0,0,.06);font-size:8.5px;color:#777;padding-left:15px;line-height:37px}
.btn-save{position:absolute;left:454px;top:351px;width:94px;height:33px;background:linear-gradient(90deg,var(--orange-deep),var(--orange-light));color:var(--white);font-family:"Montserrat",sans-serif;font-weight:700;font-size:12px;text-align:center;line-height:33px;border:0}
.export{position:absolute;top:87px;width:30px;height:30px;border-radius:50%;background:var(--white);border:1px solid var(--line);display:flex;align-items:center;justify-content:center}
.export svg{width:14px;height:14px;fill:none;stroke:#888;stroke-width:1.3}
.export.is-active{background:linear-gradient(135deg,var(--orange-deep),var(--orange-light));border:0}
.export.is-active svg{stroke:var(--white)}
.tooltip{position:absolute;left:655px;top:66px;width:31px;height:13px;background:#222;color:var(--white);font-size:6.5px;text-align:center;line-height:13px;border-radius:2px}
.tooltip::after{content:"";position:absolute;left:13px;bottom:-3px;border:3px solid transparent;border-bottom:0;border-top-color:#222}
.table-head{position:absolute;top:146px;height:32px;background:var(--orange);color:var(--white);font-family:"Montserrat",sans-serif;font-weight:700;font-size:10.5px;padding-left:14px;line-height:32px}
.table-head::after{content:"\2B0D";font-size:8px;margin-left:6px}
.row{position:absolute;left:163px;width:676px;height:33px;background:var(--white);font-size:9.5px;color:#444}
.row span{position:absolute;top:0;line-height:33px}
.show{position:absolute;left:163px;top:381px;font-family:"Montserrat",sans-serif;font-weight:500;font-size:10px;line-height:22px}
.show-select{position:absolute;left:204px;top:378px;width:43px;height:22px;border:1px solid #d6d7dc;background:var(--white);font-size:9px;color:#888;line-height:22px;padding-left:9px}
.pager{position:absolute;top:378px;font-size:14px;line-height:22px;color:#222}
.pager-current{position:absolute;left:801px;top:378px;width:22px;height:22px;border-radius:50%;background:var(--orange);color:var(--white);font-size:9px;text-align:center;line-height:22px}
</style>
</head>
<body>

<svg width="0" height="0" style="position:absolute">
  <defs>
    <symbol id="i-home" viewBox="0 0 12 12"><path d="M6 1 0.5 6h1.5v5h3V8h2v3h3V6h1.5z"/></symbol>
    <symbol id="i-chart" viewBox="0 0 12 12"><path d="M0 11h12v1H0zM1 3h1v7H1zM4 6h1.5v4H4zM7 4h1.5v6H7zM10 2h1.5v8H10z"/></symbol>
    <symbol id="i-head" viewBox="0 0 12 12"><path d="M6 1a5 5 0 0 0-5 5v4h3V7H2.5V6a3.5 3.5 0 0 1 7 0v1H8v3h3V6a5 5 0 0 0-5-5z"/></symbol>
    <symbol id="i-dollar" viewBox="0 0 12 12"><path d="M5.3 0h1.4v1.6c1.4.2 2.3 1 2.5 2.2H7.7c-.1-.6-.7-1-1.7-1s-1.6.4-1.6 1c0 .6.5.8 1.9 1.1 1.9.4 3 1 3 2.6 0 1.3-1 2.2-2.6 2.4V12H5.3v-2.1C3.7 9.7 2.7 8.8 2.6 7.5h1.5c.1.8.8 1.2 1.9 1.2 1.1 0 1.7-.4 1.7-1.1 0-.6-.5-.9-1.9-1.2C3.9 6 3 5.4 3 4c0-1.2.9-2.1 2.3-2.4z"/></symbol>
    <symbol id="i-box" viewBox="0 0 12 12"><path d="M6 .5 11 3v6L6 11.5 1 9V3zm0 1.3L2.6 3.4 6 5l3.4-1.6zM2 4.2v4.2l3.5 1.7V5.8zm8 0L6.5 5.8v4.3L10 8.4z"/></symbol>
    <symbol id="i-user" viewBox="0 0 12 12"><circle cx="6" cy="3" r="2.6"/><path d="M1.5 12V9a3 3 0 0 1 3-3h3a3 3 0 0 1 3 3v3z"/></symbol>
    <symbol id="i-menu" viewBox="0 0 12 12"><path d="M0 1.5h12v1.8H0zM0 5.1h12v1.8H0zM0 8.7h12v1.8H0z"/></symbol>
    <symbol id="i-grid" viewBox="0 0 12 12"><rect x="0" y="0" width="5.3" height="5.3" rx="1"/><rect x="6.7" y="0" width="5.3" height="5.3" rx="1"/><rect x="0" y="6.7" width="5.3" height="5.3" rx="1"/><rect x="6.7" y="6.7" width="5.3" height="5.3" rx="1"/></symbol>
    <symbol id="i-search" viewBox="0 0 12 12"><circle cx="5" cy="5" r="3.8" fill="none" stroke="#222" stroke-width="1.6"/><path d="M7.8 7.8 11 11" stroke="#222" stroke-width="1.8"/></symbol>
    <symbol id="i-gear" viewBox="0 0 16 16"><path fill="#f0912c" d="M7 0h2l.4 2.2 1.5.6 1.8-1.3 1.4 1.4-1.3 1.8.6 1.5L16 7v2l-2.2.4-.6 1.5 1.3 1.8-1.4 1.4-1.8-1.3-1.5.6L9 16H7l-.4-2.2-1.5-.6-1.8 1.3-1.4-1.4 1.3-1.8-.6-1.5L0 9V7l2.2-.4.6-1.5-1.3-1.8 1.4-1.4 1.8 1.3 1.5-.6z"/><circle cx="8" cy="8" r="2.4" fill="#fff"/></symbol>
    <symbol id="i-mail" viewBox="0 0 18 13"><rect width="18" height="13" rx="1" fill="#f07a3c"/><path d="M1 1l8 6.5L17 1M1 12l6-5M17 12l-6-5" fill="none" stroke="#fff" stroke-width="1.2"/></symbol>
    <symbol id="i-doc" viewBox="0 0 14 14"><path d="M3 1h5.5L11 3.5V13H3zM8.5 1v2.5H11M5 7h4M5 9h4M5 11h3"/></symbol>
    <symbol id="i-copy" viewBox="0 0 14 14"><rect x="4" y="3" width="7" height="10" rx="1"/><path d="M3 10V1.5h6"/></symbol>
    <symbol id="i-print" viewBox="0 0 14 14"><path d="M4 5V1h6v4M2 5h10v5H2zM4 8h6v5H4z"/></symbol>
  </defs>
</svg>

<!-- Add new suggestion -->
<section class="screen screen--form">
  <aside class="sidebar">
    <div class="brand"><span class="brand-dot"></span>Northhub</div>
    <div class="nav-item" style="top:136px"><svg><use href="#i-home"/></svg><span>Home</span></div>
    <div class="nav-item" style="top:173px"><svg><use href="#i-chart"/></svg><span>Reports</span></div>
    <div class="nav-item" style="top:210px"><svg><use href="#i-head"/></svg><span>Helpdesk</span></div>
    <div class="nav-item" style="top:247px"><svg><use href="#i-dollar"/></svg><span>Payroll</span></div>
    <div class="nav-item is-active" style="top:285px"><svg><use href="#i-box"/></svg><span>Suggestion Box</span></div>
    <div class="nav-item" style="top:322px"><svg><use href="#i-user"/></svg><span>Administrator</span></div>
  </aside>
  <header class="topbar">
    <svg class="icon" style="left:31px"><use href="#i-menu"/></svg>
    <svg class="icon" style="left:62px"><use href="#i-grid"/></svg>
    <div class="search" style="left:138px">Search...<svg><use href="#i-search"/></svg></div>
    <svg style="position:absolute;left:533px;top:20px;width:15px;height:15px"><use href="#i-gear"/></svg>
    <svg style="position:absolute;left:569px;top:21px;width:18px;height:13px"><use href="#i-mail"/></svg>
    <div class="user" style="left:617px"><div class="avatar" role="img" aria-label="User profile photo"></div>Alex Marin <small style="font-size:7px">&#8964;</small></div>
  </header>
  <h1 class="page-title">Suggestion</h1>
  <p class="crumb"><a>Home</a> &nbsp;&gt;&nbsp; Add New Suggestion</p>
  <label class="field-label" style="left:163px;top:157px">Describe Your Suggestion</label>
  <label class="field-label" style="left:508px;top:157px">How would your suggestion help us?</label>
  <div class="field" style="left:163px;top:177px">Enter Your Suggestion</div>
  <div class="field" style="left:508px;top:177px">Enter Your suggestion help</div>
  <label class="field-label" style="left:163px;top:249px">Additional Comment</label>
  <label class="field-label" style="left:508px;top:249px">Country</label>
  <div class="field" style="left:163px;top:269px">Enter Your Comment</div>
  <div class="field" style="left:508px;top:269px">Enter Your Country</div>
  <button class="btn-save">SAVE</button>
</section>

<!-- Suggestion report -->
<section class="screen screen--list">
  <aside class="sidebar">
    <div class="brand"><span class="brand-dot"></span>Northhub</div>
    <div class="nav-item" style="top:136px"><svg><use href="#i-home"/></svg><span>Home</span></div>
    <div class="nav-item is-active" style="top:173px"><svg><use href="#i-chart"/></svg><span>Reports</span></div>
    <div class="nav-sub" style="top:197px">Policy</div>
    <div class="nav-sub is-active" style="top:216px">Suggestion</div>
    <div class="nav-item" style="top:253px"><svg><use href="#i-head"/></svg><span>Helpdesk</span></div>
    <div class="nav-item" style="top:291px"><svg><use href="#i-dollar"/></svg><span>Payroll</span></div>
    <div class="nav-item" style="top:328px"><svg><use href="#i-box"/></svg><span>Suggestion Box</span></div>
    <div class="nav-item" style="top:365px"><svg><use href="#i-user"/></svg><span>Administrator</span></div>
  </aside>
  <header class="topbar">
    <svg class="icon" style="left:31px"><use href="#i-menu"/></svg>
    <svg class="icon" style="left:62px"><use href="#i-grid"/></svg>
    <div class="search" style="left:138px">Search...<svg><use href="#i-search"/></svg></div>
    <svg style="position:absolute;left:533px;top:20px;width:15px;height:15px"><use href="#i-gear"/></svg>
    <svg style="position:absolute;left:569px;top:21px;width:18px;height:13px"><use href="#i-mail"/></svg>
    <div class="user" style="left:617px"><div class="avatar" role="img" aria-label="User profile photo"></div>Alex Marin <small style="font-size:7px">&#8964;</small></div>
  </header>
  <h1 class="page-title">Suggestion</h1>
  <p class="crumb"><a>Reports</a> &nbsp;&gt;&nbsp; Suggestion</p>

  <div class="tooltip">Copy</div>
  <div class="export is-active" style="left:655px"><svg><use href="#i-copy"/></svg></div>
  <div class="export" style="left:693px"><svg><use href="#i-doc"/></svg></div>
  <div class="export" style="left:732px"><svg><use href="#i-doc"/></svg></div>
  <div class="export" style="left:770px"><svg><use href="#i-doc"/></svg></div>
  <div class="export" style="left:808px"><svg><use href="#i-print"/></svg></div>

  <div class="table-head" style="left:163px;width:128px">User Name</div>
  <div class="table-head" style="left:292px;width:127px">Description</div>
  <div class="table-head" style="left:420px;width:147px">Suggestion Help</div>
  <div class="table-head" style="left:568px;width:115px">Comments</div>
  <div class="table-head" style="left:684px;width:155px">Date</div>

  <div class="row" style="top:189px"><span style="left:14px">Super admin</span><span style="left:142px">Hola</span><span style="left:270px">Hola</span><span style="left:418px">Test</span><span style="left:534px">25 Nov 2021, 08:48Pm</span></div>
  <div class="row" style="top:229px"><span style="left:14px">Super admin</span><span style="left:142px">Hola</span><span style="left:270px">Hola</span><span style="left:418px">Hgola</span><span style="left:534px">25 Nov 2021, 02:36Am</span></div>
  <div class="row" style="top:270px"><span style="left:14px">Super admin</span><span style="left:142px">Favzxcvzcxv</span><span style="left:270px">zcxvzxcv</span><span style="left:418px">zxcvzxcvzxcv</span><span style="left:534px">24 Nov 2021, 03:22Am</span></div>
  <div class="row" style="top:311px"><span style="left:14px">Super admin</span><span style="left:142px">Hola</span><span style="left:270px">Hola</span><span style="left:418px">Hgola</span><span style="left:534px">25 Nov 2021, 02:36Am</span></div>

  <div class="show">SHOW</div>
  <div class="show-select">04 &#x2B0D;</div>
  <div class="pager" style="left:780px">&#8249;</div>
  <div class="pager-current">01</div>
  <div class="pager" style="left:832px">&#8250;</div>
</section>

</body>
</html>
```